Informational Site for Advanced Chemistry R&D

The company develops oxidation chemistry for air, water, fuel pollution controls. The site has been prototyped at www.velquaresearch.example. Take a look. Now, the task is to design it for eye-catching beauty with use of color, on-page scroll-driven color transition and parallax effects. Should capture the themes: high technology, wow it's beautiful, modern, uncluttered, clean urban environment.

Target Market(s)

China Environmentally Conscious Government and Industry,

Industry/Entity Type

It Company

Number of Pages Required

3 page

Font styles to use
Sans Serif

Requirements
Must have
• Parallax effects, desktop compatible, Rich, Modern, Simple, Graphic
Nice to have
• Mobile Phone Compatible
Should not have
• Flash, or anything that is slow to load or requires high bandwidth

```html
<!DOCTYPE html>
<html lang="en">
<head>
<meta charset="utf-8">
<title>Velqua – Advanced Oxidation</title>
<link rel="stylesheet" href="https://fonts.googleapis.com/css2?family=Open+Sans:wght@400;600;700&display=swap">
<style>
:root{
  --blue:#1c5fad;
  --blue-deep:#16509a;
  --teal:#3cc2bb;
  --teal-dark:#2aa7a8;
  --heading:#2878bf;
  --text:#555;
  --muted:#888;
  --dark:#2c2d30;
  --footer:#3b3c3e;
  --light:#f3f3f3;
  --box:#e6e6e6;
  --white:#fff;
}
*{margin:0;padding:0;box-sizing:border-box}
html,body{width:1200px;height:3536px;overflow:hidden}
body{font-family:"Open Sans",Arial,sans-serif;color:var(--text);background:var(--white);position:relative}
.abs{position:absolute}

/* header */
.site-header{position:absolute;left:0;top:0;width:1200px;height:106px;background:var(--white);border-top:4px solid var(--teal)}
.brand{position:absolute;display:flex;align-items:center;gap:12px;font-weight:700;font-size:26px;color:var(--heading)}
.brand-dot{width:30px;height:30px;border-radius:50%;background:var(--heading)}
.site-header .brand{left:118px;top:30px}
.main-nav{position:absolute;top:46px;left:0;width:1200px;font-size:13px;font-weight:600;color:#333}
.main-nav span{position:absolute;transform:translateX(-50%)}
.main-nav .active{color:var(--heading)}

/* hero */
.hero{position:absolute;left:0;top:106px;width:1200px;height:535px;background:linear-gradient(180deg,#1b3550 0%,#2d5576 35%,#4f7a86 60%,#6b9a55 85%,#4f7d3a 100%)}
.hero-panel{position:absolute;left:271px;top:118px;width:660px;height:283px;background:rgba(20,25,35,.45)}
.hero h1{position:absolute;left:0;width:1200px;top:157px;text-align:center;color:var(--white);font-size:48px;font-weight:700;letter-spacing:1px}
.hero h2{position:absolute;left:0;width:1200px;top:250px;text-align:center;color:var(--white);font-size:44px;font-weight:600;line-height:60px}
.hero-arrow{position:absolute;left:1133px;top:254px}

/* intro */
.intro-title{top:712px;left:0;width:1200px;text-align:center;color:var(--heading);font-size:21px;font-weight:600}
.intro-text{top:760px;left:0;width:1200px;text-align:center;font-size:20px;line-height:36px;color:#555}
.themes{top:880px;left:0;width:1200px;height:36px}
.theme{position:absolute;display:flex;align-items:center;gap:14px;color:var(--teal-dark);font-size:22px}

/* technology */
.technology{position:absolute;left:0;top:990px;width:1200px;height:573px;background:radial-gradient(circle at 80% 20%,#4a4c52 0%,#2c2d30 55%,#1f2022 100%)}
.tech-lead{position:absolute;left:99px;top:52px;width:580px;color:var(--white);font-size:13px;font-weight:700;line-height:27px;text-transform:uppercase}
.tech-rule{position:absolute;left:99px;top:112px;width:140px;height:2px;background:var(--white)}
.tech-points{position:absolute;left:99px;top:146px;display:flex;gap:40px;color:#ddd;font-size:13px}
.tech-points span{display:flex;align-items:center;gap:10px}
.tech-body{position:absolute;left:99px;top:188px;width:600px;color:#ddd;font-size:13px;line-height:26px}
.tech-divider{position:absolute;left:750px;top:70px;width:3px;height:166px;background:var(--white)}
.tech-title{position:absolute;left:801px;top:68px;color:var(--white);font-size:46px;font-weight:700}
.tech-sub{position:absolute;left:805px;top:132px;color:var(--white);font-size:40px;line-height:48px;letter-spacing:2px}
.tech-photo{position:absolute;top:299px;height:210px;border:3px solid #555}

/* products */
.section-title{left:0;width:1200px;text-align:center;color:var(--heading);font-size:21px;font-weight:600}
.products-wave{position:absolute;left:99px;top:1669px}
.product{position:absolute;left:170px;width:880px;color:var(--white)}
.product h3{font-size:20px;font-weight:600;text-transform:uppercase}
.product p{margin-top:14px;font-size:13px;font-weight:600;line-height:28px}
.btn{position:absolute;left:99px;width:118px;height:35px;line-height:35px;text-align:center;font-size:15px;font-weight:600;color:var(--white)}
.btn-teal{background:var(--teal)}
.btn-blue{background:var(--blue-deep)}

/* partners */
.partners-text{top:2846px;left:190px;width:820px;text-align:center;font-size:12.5px;line-height:22px;color:#555}
.badge{position:absolute;top:2925px;width:150px;height:150px;border-radius:50%;background:var(--white);box-shadow:0 4px 14px rgba(0,0,0,.18)}
.badge i{position:absolute;left:15px;top:15px;width:120px;height:120px;border-radius:50%}

/* contact */
.contact{position:absolute;left:0;top:3130px;width:1200px;height:307px;background:var(--light)}
.contact-box{position:absolute;top:130px;height:177px;background:var(--box);text-align:center}
.contact-icon{position:absolute;left:50%;top:-44px;margin-left:-44px;width:88px;height:88px;border-radius:50%;background:var(--white);display:flex;align-items:center;justify-content:center}
.contact-box h4{margin-top:58px;font-size:15px;font-weight:400;color:var(--heading)}
.contact-box p{margin-top:10px;font-size:13px;line-height:24px;color:#555}
.social{display:flex;justify-content:center;gap:10px;margin-top:16px}
.social i{width:34px;height:34px;border:2px solid #888;border-radius:50%}

/* footer */
.site-footer{position:absolute;left:0;top:3437px;width:1200px;height:99px;background:var(--footer)}
.site-footer .brand{left:130px;top:32px;color:var(--white)}
.site-footer .brand-dot{background:var(--white)}
.footer-nav{position:absolute;top:28px;left:0;width:1200px;color:var(--white);font-size:13px}
.footer-nav span{position:absolute;transform:translateX(-50%)}
.copyright{position:absolute;left:608px;top:64px;color:#bbb;font-size:13px}
</style>
</head>
<body>

<header class="site-header">
  <div class="brand"><span class="brand-dot"></span>Velqua</div>
  <nav class="main-nav">
    <span class="active" style="left:740px">HOME</span>
    <span style="left:848px">TECHNOLOGY</span>
    <span style="left:966px">PRODUCT</span>
    <span style="left:1072px">CONTACT</span>
  </nav>
</header>

<section class="hero" role="img" aria-label="Evening photograph of a modern city centre with towers, lit streets and green park lawns">
  <div class="hero-panel"></div>
  <h1>ADVANCED OXIDATION</h1>
  <h2>Science for Environmental<br>Pollution Management</h2>
  <svg class="hero-arrow" width="20" height="36" viewBox="0 0 20 36"><path d="M4 6 L15 18 L4 30" fill="none" stroke="#fff" stroke-width="3"/></svg>
</section>

<h2 class="abs intro-title">NEW IDEAS FOR A CLEANER WORLD</h2>
<p class="abs intro-text">Environmental pollution control solutions employing<br>natures most reactive free radical</p>
<div class="abs themes">
  <div class="theme" style="left:200px"><svg width="22" height="22" viewBox="0 0 22 22"><circle cx="11" cy="11" r="9" fill="none" stroke="#2aa7a8" stroke-width="2"/><path d="M6 11 l3 3 l7 -7" fill="none" stroke="#2aa7a8" stroke-width="2"/></svg>Water</div>
  <div class="theme" style="left:535px"><svg width="22" height="22" viewBox="0 0 22 22"><circle cx="11" cy="11" r="9" fill="none" stroke="#2aa7a8" stroke-width="2"/><path d="M6 11 l3 3 l7 -7" fill="none" stroke="#2aa7a8" stroke-width="2"/></svg>Air</div>
  <div class="theme" style="left:846px"><svg width="22" height="22" viewBox="0 0 22 22"><circle cx="11" cy="11" r="9" fill="none" stroke="#2aa7a8" stroke-width="2"/><path d="M6 11 l3 3 l7 -7" fill="none" stroke="#2aa7a8" stroke-width="2"/></svg>Fuel</div>
</div>

<section class="technology" role="img" aria-label="Dark background with faint molecular structure graphic">
  <p class="tech-lead">Advanced oxidation refers to a variety of techniques employing the hydroxyl radical an energetic, highly reactive cousin of the water molecule</p>
  <div class="tech-rule"></div>
  <div class="tech-points">
    <span><svg width="18" height="18" viewBox="0 0 18 18"><circle cx="9" cy="9" r="7" fill="none" stroke="#ddd" stroke-width="1.5"/><path d="M5 9 l3 3 l5 -5" fill="none" stroke="#ddd" stroke-width="1.5"/></svg>To add oxygen to Inorganic molecules</span>
    <span><svg width="18" height="18" viewBox="0 0 18 18"><circle cx="9" cy="9" r="7" fill="none" stroke="#ddd" stroke-width="1.5"/><path d="M5 9 l3 3 l5 -5" fill="none" stroke="#ddd" stroke-width="1.5"/></svg>To remove hydrogen from organic molecules</span>
  </div>
  <p class="tech-body">These transformations convert important industrial contaminants into reactive forms that can be captured or that disintegrate into harmless end products.</p>
  <div class="tech-divider"></div>
  <h2 class="tech-title">TECHNOLOGY</h2>
  <p class="tech-sub">Advanced<br>Oxidation</p>
  <div class="tech-photo" style="left:106px;width:325px;background:linear-gradient(180deg,#5d6478,#3a3f52 60%,#22252f)" role="img" aria-label="Industrial chimneys releasing smoke"></div>
  <div class="tech-photo" style="left:438px;width:321px;background:linear-gradient(180deg,#5a6a80,#3d4e66 55%,#7a8590)" role="img" aria-label="Technician working beside a water treatment tank"></div>
  <div class="tech-photo" style="left:766px;width:325px;background:linear-gradient(180deg,#8a8f96,#4a4f57 55%,#2b2e33)" role="img" aria-label="Pipework and towers of a refinery plant"></div>
</section>

<h2 class="abs section-title" style="top:1615px">OUR PRODUCTS</h2>
<svg class="products-wave" width="1002" height="1112" viewBox="0 0 1002 1112">
  <path d="M0,0 C200,90 400,-20 600,30 S900,60 1002,40 L1002,1112 C700,1000 300,1080 0,1020 Z" fill="#1c5fad"/>
  <path d="M0,280 C250,380 450,200 700,260 S950,330 1002,300 L1002,1112 C700,1000 300,1080 0,1020 Z" fill="#3cc2bb"/>
  <path d="M0,560 C250,470 500,620 750,560 S950,520 1002,540 L1002,1112 C700,1000 300,1080 0,1020 Z" fill="#1c5fad"/>
  <path d="M0,830 C250,760 500,880 750,820 S950,770 1002,800 L1002,1112 C700,1000 300,1080 0,1020 Z" fill="#3cc2bb"/>
  <g fill="none" stroke="#fff" stroke-width="6">
    <path d="M0,280 C250,380 450,200 700,260 S950,330 1002,300"/>
    <path d="M0,560 C250,470 500,620 750,560 S950,520 1002,540"/>
    <path d="M0,830 C250,760 500,880 750,820 S950,770 1002,800"/>
  </g>
</svg>

<div class="product" style="top:1772px">
  <h3>FGAO</h3>
  <p>Our proprietary low temperature and pressure advanced oxidation catalytic process reliably removes sulfur from diesel transportation fuel at less than half the operating costs of older hydro-desulfurization processes.</p>
  <span class="btn btn-teal" style="top:124px">Read more</span>
</div>
<div class="product" style="top:2027px">
  <h3>Volatile organic compunds (VOC)</h3>
  <p>Alkanes, alkenes, halogenated hydrocarbons, aromatic hydrocarbons, esters, aldehydes, polycyclic aromatic hydrocarbons. We convert these by-products of industrial processes before they enter the atmosphere and cause smog.</p>
  <span class="btn btn-blue" style="top:120px">Read more</span>
</div>
<div class="product" style="top:2279px">
  <h3>Flue gas scrubbing</h3>
  <p>Desulfurization and denitrification using our proprietary flue gas advanced oxidation catalytic process (FGAOC). Sulfur and nitrogen are oxidized and adsorbed into an environmentally friendly solid medium for safe removal from site.</p>
  <span class="btn btn-teal" style="top:129px">Read more</span>
</div>
<div class="product" style="top:2545px">
  <h3>Wastewater treatment</h3>
  <p>Photoelectrocatalysed (PEC) anodic oxidation removes soluble organics. Novel anode design using our proprietary nano-carbon surface operates non-selectively to remove 99% of contaminants across a wide range of chemical oxygen demand.</p>
  <span class="btn btn-blue" style="top:130px">Read more</span>
</div>

<h2 class="abs section-title" style="top:2798px">OUR PARTNERS</h2>
<p class="abs partners-text">Our research partners include leading universities and engineering firms that share a commitment to cleaner air, water and fuel, working with us from laboratory study to full scale field deployment.</p>
<div class="badge" style="left:234px"><i style="background:#c9232c"></i></div>
<div class="badge" style="left:425px"><i style="background:#2aa7a8"></i></div>
<div class="badge" style="left:616px"><i style="background:#1f3f86"></i></div>
<div class="badge" style="left:811px"><i style="background:#d8342a"></i></div>

<section class="contact">
  <h2 class="abs section-title" style="top:33px">CONTACT INFO</h2>
  <div class="contact-box" style="left:99px;width:250px">
    <div class="contact-icon"><svg width="30" height="30" viewBox="0 0 30 30"><path d="M3 15 L15 4 L27 15 H23 V26 H18 V19 H12 V26 H7 V15 Z" fill="#2aa7a8"/></svg></div>
    <h4>ADDRESS</h4>
    <p>Velqua Research Corp. Harbor Point,<br>Oregon, U.S.A.</p>
  </div>
  <div class="contact-box" style="left:356px;width:238px">
    <div class="contact-icon"><svg width="30" height="30" viewBox="0 0 30 30"><path d="M7 3 L12 8 L9 12 C11 17 13 19 18 21 L22 18 L27 23 L23 27 C13 26 4 17 3 7 Z" fill="#2aa7a8"/></svg></div>
    <h4>CALL US</h4>
    <p>+1 555 014 2290<br>(555) - 0142 - 7731</p>
  </div>
  <div class="contact-box" style="left:606px;width:238px">
    <div class="contact-icon"><svg width="32" height="26" viewBox="0 0 32 26"><rect x="2" y="3" width="28" height="20" fill="none" stroke="#2aa7a8" stroke-width="2.5"/><path d="M2 4 L16 15 L30 4" fill="none" stroke="#2aa7a8" stroke-width="2.5"/></svg></div>
    <h4>EMAIL US</h4>
    <p>info@velquaresearch.example<br>lab@velquaresearch.example</p>
  </div>
  <div class="contact-box" style="left:856px;width:245px">
    <div class="contact-icon"><svg width="30" height="30" viewBox="0 0 30 30"><circle cx="15" cy="15" r="12" fill="#2aa7a8"/><path d="M3 15 H27 M15 3 C9 10 9 20 15 27 M15 3 C21 10 21 20 15 27" fill="none" stroke="#fff" stroke-width="1.6"/></svg></div>
    <h4>SOCIAL LINKS</h4>
    <div class="social"><i></i><i></i><i></i><i></i></div>
  </div>
</section>

<footer class="site-footer">
  <div class="brand"><span class="brand-dot"></span>Velqua</div>
  <nav class="footer-nav">
    <span style="left:625px">HOME</span>
    <span style="left:690px">•</span>
    <span style="left:766px">TECHNOLOGY</span>
    <span style="left:842px">•</span>
    <span style="left:919px">PRODUCT</span>
    <span style="left:990px">•</span>
    <span style="left:1061px">CONTACT</span>
  </nav>
  <p class="copyright">All Rights Reserved . copyright 2016 velquaresearch.example</p>
</footer>

</body>
</html>
```